MS word document templates for consultancy

I need the following templates for my business using my logo as branding.

- General report template
- Letter head template
- Tender proposal template

The templates should be sleek and with minimal colors, but with a small amount of green and grey where appropriate (as per attached logo and email signature). Font should be consistent with the text in the email signature.

```html
<!DOCTYPE html>
<html lang="en">
<head>
<meta charset="utf-8">
<title>Northwise Partners – Letterhead and Report Templates</title>
<link rel="stylesheet" href="https://fonts.googleapis.com/css2?family=Arimo:wght@400;700&family=Roboto:wght@400;500;700&family=Roboto+Condensed:wght@500;600&display=swap">
<style>
  :root {
    --backdrop: #9d9d9d;
    --paper: #ffffff;
    --ink: #1f1f1f;
    --body-text: #555555;
    --rule: #b5b5b5;
    --brand-green: #2a9644;
    --band-dark: #1e1e1e;
    --signature-tone: #e6e6e6;
  }
  * { margin: 0; padding: 0; box-sizing: border-box; }
  html, body { width: 1200px; height: 982px; overflow: hidden; }
  body { background: var(--backdrop); position: relative; font-family: "Arimo", Arial, sans-serif; }

  .page {
    position: absolute; top: 130px; width: 511px; height: 722px;
    background: var(--paper);
    box-shadow: 2px 3px 6px rgba(0,0,0,.35);
  }
  .page--letter { left: 72px; }
  .page--report { left: 617px; }

  .brand {
    position: absolute; top: 38px; left: 0; width: 100%;
    display: flex; justify-content: center; align-items: center; gap: 7px;
  }
  .brand__mark { width: 9px; height: 9px; background: var(--brand-green); }
  .brand__name {
    font-family: "Roboto", sans-serif; font-weight: 400; font-size: 22px;
    color: var(--ink); letter-spacing: .2px;
  }

  .copy p {
    font-size: 8.7px; line-height: 10.5px; color: var(--body-text);
    margin-bottom: 9px;
  }

  /* Letter */
  .letter__salutation {
    position: absolute; left: 47px; top: 222px;
    font-size: 12px; color: var(--body-text);
  }
  .letter__body { position: absolute; left: 46px; top: 255px; width: 420px; }
  .letter__body p { margin-bottom: 9.5px; }
  .letter__closing {
    position: absolute; left: 47px; top: 472px;
    font-size: 6.5px; color: var(--body-text);
  }
  .letter__signature {
    position: absolute; left: 46px; top: 492px; width: 66px; height: 22px;
    background: var(--signature-tone); border-radius: 2px;
  }

  /* Report */
  .report__banner {
    position: absolute; left: 46px; top: 109px; width: 415px; height: 41px;
    background: var(--brand-green); color: #fff;
    font-family: "Roboto", sans-serif; font-weight: 500; font-size: 33px;
    letter-spacing: 1px; text-align: center; line-height: 41px;
  }
  .report__section { position: absolute; left: 46px; width: 418px; }
  .report__heading {
    font-family: "Roboto Condensed", sans-serif; font-weight: 600; font-size: 17.5px;
    color: var(--brand-green); line-height: 18px;
    border-bottom: 1px solid var(--rule); padding-bottom: 1px; margin-bottom: 6px;
    width: 415px;
  }

  /* Footer band */
  .footer { position: absolute; left: 0; top: 678px; width: 511px; height: 30px; }
  .footer__band { position: absolute; inset: 0; }
  .footer__contact {
    position: absolute; left: 0; width: 510px; top: 9px; text-align: center;
    font-family: "Roboto", sans-serif; font-size: 8.5px; color: #fff; letter-spacing: .1px;
  }
  .footer__contact strong { font-weight: 700; }
  .footer__phone-icon { display: inline-block; vertical-align: -1px; margin-right: 2px; }
</style>
</head>
<body>

<section class="page page--letter" aria-label="Letterhead template">
  <header class="brand">
    <span class="brand__mark"></span>
    <span class="brand__name">Northwise Partners</span>
  </header>

  <p class="letter__salutation">Dear Mr. Carter,</p>

  <div class="letter__body copy">
    <p>Lorem ipsum dolor sit amet, consectetuer adipiscing elit, sed diam nonmmy nibh euismod tincidunt ut laor eet dolore magna aliquam erat volutpat. Ut wisi enim ad minim veniam, quis nostrud exerci tationmcorper suscipit lobortis nisl ut aliquip ex ea commodo consequat. Duis autem vel eum iriure dolor in hendrerit in vulputate velit esse molestie consequat, vel illum dolore eu feugiat</p>
    <p>Rorem ipsum dolor sit amet, consectetuer adipiscing elit, sed diam nonmmy nibh euismod tincidunt ut laor eet dolore magna aliquam erat volutpat. Ut wisi enim ad minim veniam, quis nostrud exerci tationmcorper suscipit lobortis nisl ut aliquip ex ea commodo consequat. Duis autem vel eum iriure dolor in hendrerit in vulputate velit esse molest</p>
    <p>Dorem ipsum dolor sit amet, consectetuer adipiscing elit, sed diam nonmmy nibh euismod tincidunt ut laor eet dolore magna aliquam erat volutpat. Ut wisi enim ad minim veniam, quis nostrud exerci tationmcorper suscipit lobortis nisl ut aliquip ex ea commodo consequat. Duis autem vel eum iriure dolor in hendrerit in suscipit lobortis nisl ut aliquip ex ea commodo consequat. Duis autem vel eum iriure dolor in hendrerit in vulputate velit esse molestie consequat, vel illum</p>
    <p>Sorem ipsum dolor sit amet, consectetuer adipiscing elit, sed diam nonmmy nibh euismod tincidunt ut laor eet dolore magna aliquam erat volutpat. Ut wisi enim ad minim veniam, quis nostrud exerci tationmcorper suscipit lobortis nisl ut aliquip ex ea commodo consequat. Duis autem vel eum iriure dolor in</p>
  </div>

  <p class="letter__closing">Sincerely,</p>
  <div class="letter__signature" role="img" aria-label="Handwritten signature"></div>

  <footer class="footer">
    <svg class="footer__band" width="511" height="30" viewBox="0 0 511 30" aria-hidden="true">
      <polygon points="0,4 445,4 430,19 0,19" fill="var(--band-dark)"/>
      <polyline points="0,25.5 445,25.5 470,4" fill="none" stroke="var(--brand-green)" stroke-width="3"/>
    </svg>
    <p class="footer__contact"><strong>Daniel Reeve |</strong> Managing Director <strong>|</strong>
      <svg class="footer__phone-icon" width="7" height="7" viewBox="0 0 10 10" aria-hidden="true"><path d="M1 3 Q5 0 9 3 L8 4.5 L6.5 3.8 L6.5 3 Q5 2.6 3.5 3 L3.5 3.8 L2 4.5 Z M2.5 5 H7.5 L8.5 9 H1.5 Z" fill="var(--brand-green)"/></svg>0400 555 019</p>
  </footer>
</section>

<section class="page page--report" aria-label="Report template">
  <header class="brand">
    <span class="brand__mark"></span>
    <span class="brand__name">Northwise Partners</span>
  </header>

  <h1 class="report__banner">ANNUAL REPORT 2025</h1>

  <section class="report__section copy" style="top:167px">
    <h2 class="report__heading">Title:</h2>
    <p>Lorem ipsum dolor sit amet, consectetuer adipiscing elit, sed diam nonmmy nibh euismod tincidunt ut laor eet dolore magna aliquam erat volutpat. Ut wisi enim ad minim veniam, quis nostrud exerci tationmcorper suscipit lobortis nisl ut aliquip ex ea commodo consequat. Duis autem vel eum iriure dolor in hendrerit in vulputate velit esse molestie consequat, vel illum dolore eu feugiat</p>
  </section>

  <section class="report__section copy" style="top:249px">
    <h2 class="report__heading">Table of contents:</h2>
    <p>Lorem ipsum dolor sit amet, consectetuer adipiscing elit, sed diam nonmmy nibh euismod tincidunt ut laor eet dolore magna aliquam erat volutpat. Ut wisi enim ad minim veniam, quis nostrud exerci tationmcorper suscipit lobortis nisl ut aliquip ex ea commodo consequat. Duis autem vel eum iriure dolor in hendrerit in vulputate velit esse molestie consequat, vel illum dolore eu feugiat</p>
    <p>Rorem ipsum dolor sit amet, consectetuer adipiscing elit, sed diam nonmmy nibh euismod tincidunt ut laor eet dolore magna aliquam erat volutpat. Ut wisi enim ad minim veniam, quis nostrud exerci tationmcorper suscipit lobortis nisl ut aliquip ex ea commodo consequat. Duis autem vel eum iriure dolor in hendrerit in vulputate velit esse molest</p>
  </section>

  <section class="report__section copy" style="top:381px">
    <h2 class="report__heading">Executive Summary:</h2>
    <p>Lorem ipsum dolor sit amet, consectetuer adipiscing elit, sed diam nonmmy nibh euismod tincidunt ut laor eet dolore magna aliquam erat volutpat. Ut wisi enim ad minim veniam, quis nostrud exerci tationmcorper suscipit lobortis nisl ut aliquip ex ea commodo consequat. Duis autem vel eum iriure dolor in hendrerit in vulputate velit esse molestie consequat, vel illum dolore eu feugiat</p>
  </section>

  <section class="report__section copy" style="top:465px">
    <h2 class="report__heading">Quick Summary (Introduction):</h2>
    <p>Lorem ipsum dolor sit amet, consectetuer adipiscing elit, sed diam nonmmy nibh euismod tincidunt ut laor eet dolore magna aliquam erat volutpat. Ut wisi enim ad minim veniam, quis nostrud exerci tationmcorper suscipit lobortis nisl ut aliquip ex ea commodo consequat. Duis autem vel eum iriure dolor in hendrerit in vulputate velit esse molestie consequat, vel illum dolore eu feugiat</p>
    <p>Rorem ipsum dolor sit amet, consectetuer adipiscing elit, sed diam nonmmy nibh euismod tincidunt ut laor eet dolore magna aliquam erat volutpat. Ut wisi enim ad minim veniam, quis nostrud exerci tationmcorper suscipit lobortis nisl ut aliquip ex ea commodo consequat. Duis autem vel eum iriure dolor in hendrerit in vulputate velit esse molest</p>
  </section>

  <section class="report__section copy" style="top:593px">
    <h2 class="report__heading">Conclusion:</h2>
    <p>Lorem ipsum dolor sit amet, consectetuer adipiscing elit, sed diam nonmmy nibh euismod tincidunt ut laor eet dolore magna aliquam erat volutpat. Ut wisi enim ad minim veniam, quis nostrud exerci tationmcorper suscipit lobortis nisl ut aliquip ex ea commodo consequat. Duis autem vel eum iriure dolor in hendrerit in vulputate velit esse molestie consequat, vel illum dolore eu feugiat</p>
  </section>

  <footer class="footer">
    <svg class="footer__band" width="511" height="30" viewBox="0 0 511 30" aria-hidden="true">
      <polygon points="0,4 445,4 430,19 0,19" fill="var(--band-dark)"/>
      <polyline points="0,25.5 445,25.5 470,4" fill="none" stroke="var(--brand-green)" stroke-width="3"/>
    </svg>
    <p class="footer__contact"><strong>Daniel Reeve |</strong> Managing Director <strong>|</strong>
      <svg class="footer__phone-icon" width="7" height="7" viewBox="0 0 10 10" aria-hidden="true"><path d="M1 3 Q5 0 9 3 L8 4.5 L6.5 3.8 L6.5 3 Q5 2.6 3.5 3 L3.5 3.8 L2 4.5 Z M2.5 5 H7.5 L8.5 9 H1.5 Z" fill="var(--brand-green)"/></svg>0400 555 019</p>
  </footer>
</section>

</body>
</html>
```